New Business Card Design for Manufacturing

We are an engineering/manufacturing company that offers Advanced machining/assembly/engineering services, as well as innovative products for the heavy duty engine cooling markets.

We are looking to get a new business card designed that is clean and modern looking, but still fits the wide range of technical/skilled work we do.

- We hope to use this design as the base for other design work in new Presentations, web, and print work.

Industry/Entity Type

Engineering

Contact Information for Business Card

Our preferred color of blue is (RGB) 22/71/159 but can vary slightly from that color. Our content will be our Logo and full company name (Vantrell Forge Works, Inc.), company address, name, job title, phone number with extension, cell number, fax number, website, and email address on the cards.
We'd like the full company name next to the logo, but we are open to other interpretations of that layout.
Preferably, we would like the back side to be clean with just our logo, and the front to contain all of the contact information.

Colors
2f74b4
0355a3
85abd2

Requirements
Must have
• - Logo, company name, needed content - We are open to interpretation beyond that.
• - Standard size business card.
• - Horizontal orientation.
• - Enough space for lengthy names / job titles (for example, a job title could read "Directory of Human Resources" or "V.P. of Governmental Affairs"). We need this to look clean, whether the title be short (CEO) or long (as described above).

```html
<!DOCTYPE html>
<html lang="en">
<head>
<meta charset="utf-8">
<title>Vantrell Forge Works – Business Card</title>
<link href="https://fonts.googleapis.com/css2?family=Exo+2:wght@400;700;800&display=swap" rel="stylesheet">
<style>
  :root {
    --brand-blue: #16479f;
    --card-black: #0b0b0c;
    --card-white: #ffffff;
    --ink: #111111;
    --text-light: #e9e9ea;
    --backdrop: #e7e5e1;
  }
  * { box-sizing: border-box; margin: 0; padding: 0; }
  html, body {
    width: 1200px; height: 800px; overflow: hidden;
    background: var(--backdrop);
    font-family: "Exo 2", Arial, sans-serif;
  }
  .canvas { position: relative; width: 1200px; height: 800px; }
  .card {
    position: absolute; top: 252px;
    width: 520px; height: 297px;
    overflow: hidden;
    box-shadow: 0 10px 28px rgba(0,0,0,.18);
  }
  /* Logo side */
  .card--logo {
    left: 60px; background: var(--card-white);
    display: flex; flex-direction: column; align-items: center; justify-content: center;
    padding: 0 30px;
  }
  .brand-name {
    color: var(--brand-blue); font-weight: 800;
    font-size: 34px; letter-spacing: 1px; text-transform: uppercase; line-height: 1;
    white-space: nowrap;
  }
  .brand-tagline {
    margin-top: 12px; color: var(--ink); font-weight: 800;
    font-size: 18px; letter-spacing: .5px; text-transform: uppercase;
  }
  /* Contact side */
  .card--contact { left: 620px; background: var(--card-black); color: var(--text-light); }
  .person {
    position: absolute; left: 40px; top: 36px;
    padding-left: 16px; border-left: 5px solid var(--brand-blue);
  }
  .person__name { font-weight: 700; font-size: 17px; letter-spacing: .5px; color: #fff; text-transform: uppercase; }
  .person__title { font-size: 14px; margin-top: 2px; }
  .contact-list { position: absolute; left: 40px; list-style: none; font-size: 13px; }
  .contact-list li { display: flex; align-items: center; gap: 10px; height: 20px; }
  .contact-list svg { width: 13px; height: 13px; fill: none; stroke: var(--text-light); stroke-width: 1.6; }
  .contact-list--phones { top: 100px; }
  .contact-list--web { top: 176px; }
  .address { position: absolute; left: 40px; top: 230px; font-size: 13px; line-height: 1.5; }
  .brand-vertical {
    position: absolute; right: 30px; top: 24px; bottom: 44px; width: 30px;
    display: flex; align-items: center; justify-content: center;
  }
  .brand-vertical span {
    writing-mode: vertical-rl; transform: rotate(180deg);
    white-space: nowrap;
    font-weight: 800; font-size: 15px; letter-spacing: .5px; color: #fff; text-transform: uppercase;
  }
  .accent-bar {
    position: absolute; right: 30px; bottom: 22px;
    width: 90px; height: 6px; background: var(--brand-blue);
  }
</style>
</head>
<body>
<main class="canvas">
  <section class="card card--logo" aria-label="Business card, logo side">
    <p class="brand-name">Vantrell Forge Works</p>
    <p class="brand-tagline">Built for What's Next</p>
  </section>

  <section class="card card--contact" aria-label="Business card, contact side">
    <div class="person">
      <p class="person__name">Jordan Reyes</p>
      <p class="person__title">Directory of Human Resources</p>
    </div>

    <ul class="contact-list contact-list--phones">
      <li><svg viewBox="0 0 14 14"><rect x="3.5" y="1" width="7" height="12" rx="1.2"/></svg>555-210-4408</li>
      <li><svg viewBox="0 0 14 14"><path d="M3 1.5l2 2.5-1.2 1.5a7 7 0 0 0 4.7 4.7L10 9l2.5 2-1 2C6 13 1 8 1 2.5z"/></svg>555-210-4400 x12</li>
      <li><svg viewBox="0 0 14 14"><rect x="1" y="5" width="12" height="6"/><rect x="3.5" y="1.5" width="7" height="3.5"/><rect x="3.5" y="9" width="7" height="3.5"/></svg>555-210-4499</li>
    </ul>

    <ul class="contact-list contact-list--web">
      <li><svg viewBox="0 0 14 14"><rect x="1" y="3" width="12" height="8"/><path d="M1 3l6 5 6-5"/></svg>jreyes@vantrellforge.com</li>
      <li><svg viewBox="0 0 14 14"><circle cx="7" cy="7" r="6"/><ellipse cx="7" cy="7" rx="2.6" ry="6"/><path d="M1 7h12"/></svg>www.vantrellforge.com</li>
    </ul>

    <p class="address">418 Corwell<br>Avenue Harlow, MA 01862</p>

    <div class="brand-vertical"><span>Vantrell Forge Works</span></div>
    <div class="accent-bar"></div>
  </section>
</main>
</body>
</html>
```